Bright Nook Home Page (A Home Wellness e-commerce site & blog)

We need a dynamic home page created for a home wellness brand. Must be visually appealing and extremely mobile-friendly. Logos and a Navmap have been provided but that is just a guideline, PLEASE USE YOUR CREATIVITY.

Target Market(s)

1st target demo: females 24-48, 2nd target demo: all 24-48

Number of Pages Required

1 page

```html
<!DOCTYPE html>
<html lang="en">
<head>
<meta charset="utf-8">
<title>Bright Nook – Home</title>
<link href="https://fonts.googleapis.com/css2?family=Roboto:wght@400;500;700&family=Lato:wght@400;700&display=swap" rel="stylesheet">
<style>
:root{
  --teal:#2fb5bf;
  --teal-dark:#23a3ad;
  --purple:#3a1d8c;
  --ink:#111;
  --text:#333;
  --muted:#777;
  --aqua:#b6e6e8;
  --footer:#111;
}
*{margin:0;padding:0;box-sizing:border-box}
html,body{width:1200px;height:3322px;overflow:hidden;background:#fff}
body{font-family:'Lato',sans-serif;color:var(--text);position:relative}
.abs{position:absolute}
.topbar{left:0;top:0;width:1200px;height:39px;background:var(--teal);color:#fff;font:500 15px 'Roboto',sans-serif}
.topbar .phone{left:112px;top:10px;display:flex;gap:8px;align-items:center}
.topbar .promo{left:0;width:1200px;top:10px;text-align:center}
.topbar .social{right:112px;top:12px;display:flex;gap:26px}
.dot{width:12px;height:12px;border-radius:50%;background:#fff;display:block}
.header{left:0;top:39px;width:1200px;height:84px;background:#fff}
.brand{font:700 33px 'Roboto',sans-serif;color:var(--ink);display:flex;align-items:center;gap:8px}
.brand i{width:12px;height:12px;background:var(--teal);border-radius:50%;display:block}
.header .brand{left:108px;top:20px}
.nav{left:340px;top:27px;display:flex;gap:46px;font:400 15px 'Roboto',sans-serif;color:#222}
.nav a{color:inherit;text-decoration:none}
.nav .active{color:var(--teal)}
.tools{left:964px;top:26px;display:flex;gap:24px;align-items:center}
.badge{position:absolute;right:-6px;top:-6px;width:13px;height:13px;border-radius:50%;background:#111;color:#fff;font:700 8px/13px 'Roboto',sans-serif;text-align:center}
.hero{left:0;top:123px;width:1200px;height:600px;background:linear-gradient(180deg,#8a7d6a 0%,#b8945a 45%,#a06f33 80%,#7a5a33 100%)}
.hero-inner{left:0;top:257px;width:1200px;text-align:center;color:#fff}
.hero h1{font:700 53px 'Roboto',sans-serif;letter-spacing:1px}
.hero p{font:400 15px 'Lato',sans-serif;margin-top:14px}
.btn-purple{display:inline-flex;gap:12px;align-items:center;background:var(--purple);color:#fff;font:500 16px 'Roboto',sans-serif;padding:12px 24px;margin-top:24px}
.arrow-circle{top:328px;width:33px;height:33px;border-radius:50%;background:var(--teal);display:flex;align-items:center;justify-content:center}
.sale{left:181px;top:676px;width:838px;height:106px;background:linear-gradient(100deg,var(--teal) 0%,#4cc3cb 50%,var(--teal) 100%);box-shadow:0 6px 14px rgba(0,0,0,.15);color:#fff;text-align:center;font:500 21px/31px 'Roboto',sans-serif;padding-top:22px}
.section-title{left:0;width:1200px;text-align:center}
.section-title h2{font:700 39px 'Roboto',sans-serif;color:var(--ink)}
.section-title .rule{width:80px;height:4px;background:var(--teal);margin:14px auto 0}
.section-title p{font:500 20px 'Roboto',sans-serif;color:var(--purple);margin-top:24px}
.gallery{left:160px;top:998px;width:880px;height:467px;display:grid;grid-template-columns:244px 244px 372px;grid-template-rows:149px 149px 149px;gap:10px}
.tile{position:relative;display:flex;align-items:flex-end;justify-content:center;color:#fff;font:400 15px/21px 'Roboto',sans-serif;text-align:center;padding-bottom:24px}
.t1{background:linear-gradient(135deg,#e6e6e4,#c8a28a)}
.t2{background:linear-gradient(135deg,#c27a3d,#7d4f2a)}
.t3{grid-row:1/3;grid-column:3;background:linear-gradient(135deg,#f4d5cb,#d9a98c)}
.t4{background:linear-gradient(135deg,#e9dcc5,#8c6a44)}
.t5{background:linear-gradient(135deg,#e9eceb,#9a8a78)}
.t6{background:linear-gradient(135deg,#e2e4e6,#bfc3c6)}
.t7{background:linear-gradient(135deg,#6c5a48,#3f342a)}
.t8{background:linear-gradient(135deg,#5d6b55,#8a8a7a)}
.zoom{position:absolute;left:108px;top:62px;width:28px;height:28px;border-radius:50%;background:var(--purple)}
.about{left:0;top:1556px;width:1200px;height:424px;background:linear-gradient(90deg,#a9d8db 0%,#b9e6e8 45%,var(--aqua) 100%)}
.about-photo{left:0;top:0;width:520px;height:424px;background:linear-gradient(135deg,#d6ecec 0%,#9cc8ca 55%,#c9c07a 100%)}
.about-body{left:579px;top:50px;width:520px}
.about-body h2{font:700 39px 'Roboto',sans-serif;color:var(--ink)}
.about-body .rule{width:80px;height:4px;background:var(--ink);margin-top:14px}
.about-body p{font:400 15px/29px 'Lato',sans-serif;color:#333;margin-top:30px}
.btn-outline{display:inline-flex;gap:12px;align-items:center;border:1.5px solid #222;color:#222;font:500 16px 'Roboto',sans-serif;padding:10px 20px;margin-top:32px}
.card{top:2212px;width:302px;height:372px;background:#fff;box-shadow:0 2px 10px rgba(0,0,0,.12)}
.card .img{height:152px}
.card .body{padding:22px 22px 0}
.card h3{font:500 15px 'Roboto',sans-serif;color:#111}
.meta{display:flex;gap:22px;margin-top:16px;font:400 15px 'Lato',sans-serif;color:var(--teal)}
.meta span{display:flex;gap:8px;align-items:center}
.card p{font:400 15px/26px 'Lato',sans-serif;color:var(--muted);margin-top:12px}
.more{margin-top:12px;font:500 15px 'Roboto',sans-serif;color:var(--teal);display:flex;gap:12px;align-items:center}
.c1 .img{background:linear-gradient(135deg,#e85a78,#f4c9cf)}
.c2 .img{background:linear-gradient(135deg,#e4e2dd,#b8a992)}
.c3 .img{background:linear-gradient(135deg,#c59a66,#8a5a2e)}
.paylater{left:0;top:2661px;width:1200px;height:285px;background:linear-gradient(90deg,#32aeb7,#3cb8c0 50%,#31adb6);color:#fff;text-align:center}
.paylater h2{font:700 39px 'Roboto',sans-serif;margin-top:42px}
.paylater .rule{width:80px;height:4px;background:#fff;margin:14px auto 0}
.paylater p{font:400 15px/26px 'Lato',sans-serif;margin:24px auto 0;width:640px}
.payname{display:inline-flex;gap:10px;align-items:center;font:700 35px 'Roboto',sans-serif;margin-top:24px}
.payname i{width:34px;height:34px;border-radius:50%;background:var(--purple);display:block}
.footer{left:0;top:2946px;width:1200px;height:376px;background:var(--footer);color:#fff}
.footer .brand{left:111px;top:46px;color:#fff;font-size:27px}
.footer .social{left:111px;top:110px;display:flex;gap:22px}
.fcol{top:53px}
.fcol h4{font:500 17px 'Roboto',sans-serif;color:var(--teal)}
.fcol ul{list-style:none;margin-top:26px}
.fcol li{font:400 15px 'Lato',sans-serif;height:34.5px}
.news p{font:400 15px/26px 'Lato',sans-serif;margin-top:18px;width:280px}
.email{width:278px;height:41px;background:#fff;margin-top:18px;display:flex;align-items:center;gap:12px;padding-left:16px;color:#888;font:400 13px 'Lato',sans-serif}
.submit{width:151px;height:41px;background:var(--purple);margin-top:26px;display:flex;align-items:center;justify-content:center;gap:12px;font:500 16px 'Roboto',sans-serif}
.divider{left:111px;top:298px;width:978px;height:1px;background:#444}
.copy{left:0;width:1200px;top:325px;text-align:center;font:400 15px 'Lato',sans-serif}
.chat{left:1040px;top:310px}
</style>
</head>
<body>

<div class="abs topbar">
  <div class="abs phone">
    <svg width="14" height="14" viewBox="0 0 24 24" fill="#fff"><path d="M6.6 10.8a15 15 0 0 0 6.6 6.6l2.2-2.2a1 1 0 0 1 1-.25 11 11 0 0 0 3.6.6 1 1 0 0 1 1 1V20a1 1 0 0 1-1 1A17 17 0 0 1 3 4a1 1 0 0 1 1-1h3.5a1 1 0 0 1 1 1c0 1.25.2 2.45.6 3.6a1 1 0 0 1-.25 1z"/></svg>
    555 (210) 764
  </div>
  <div class="abs promo">‘Free shipping on all orders $50 and over!”</div>
  <div class="abs social"><span class="dot"></span><span class="dot"></span><span class="dot"></span></div>
</div>

<header class="abs header">
  <div class="abs brand"><i></i>BrightNook</div>
  <nav class="abs nav">
    <a class="active">HOME</a><a>ABOUT US</a><a>FEATURED PRODUCT</a><a>BLOG</a><a>CONTACT US</a>
  </nav>
  <div class="abs tools">
    <svg width="22" height="22" viewBox="0 0 24 24" fill="none" stroke="#2fb5bf" stroke-width="3"><circle cx="10" cy="10" r="7"/><path d="M15 15l6 6"/></svg>
    <svg width="20" height="22" viewBox="0 0 24 24" fill="#2fb5bf"><circle cx="12" cy="7" r="5"/><path d="M3 23c0-6 4-9 9-9s9 3 9 9z"/></svg>
    <span style="position:relative;display:block">
      <svg width="24" height="22" viewBox="0 0 24 22" fill="#2fb5bf"><path d="M0 1h4l3 12h13l3-9H6" stroke="#2fb5bf" stroke-width="2" fill="none"/><path d="M6 4h17l-3 9H8z"/><circle cx="9" cy="19" r="2"/><circle cx="19" cy="19" r="2"/></svg>
      <span class="badge">0</span>
    </span>
  </div>
</header>

<section class="abs hero" role="img" aria-label="A smiling family running hand in hand through a golden wheat field at sunset">
  <div class="abs arrow-circle" style="left:44px"><svg width="12" height="12" viewBox="0 0 12 12" fill="none" stroke="#fff" stroke-width="2"><path d="M8 1L3 6l5 5"/></svg></div>
  <div class="abs arrow-circle" style="left:1124px"><svg width="12" height="12" viewBox="0 0 12 12" fill="none" stroke="#fff" stroke-width="2"><path d="M4 1l5 5-5 5"/></svg></div>
  <div class="abs hero-inner">
    <h1>BRIGHT NOOK</h1>
    <p>At Bright Nook we believe that home shoul&nbsp; be your place of Zen.</p>
    <span class="btn-purple">Shop Now <svg width="12" height="12" viewBox="0 0 12 12" fill="none" stroke="#fff" stroke-width="2"><path d="M1 2l4 4-4 4M6 2l4 4-4 4"/></svg></span>
  </div>
</section>

<div class="abs sale">50% off sale going on now! Because saving<br>money also makes us happy</div>

<div class="abs section-title" style="top:852px">
  <h2>FEATURED PRODUCT</h2>
  <div class="rule"></div>
  <p>The key to total bliss is nurturing the mind, body, and soul</p>
</div>

<div class="abs gallery">
  <div class="tile t1" role="img" aria-label="Jade face roller on a copper dish beside a jar of cream"></div>
  <div class="tile t2" role="img" aria-label="Massage stones, rolled towel and bath salt on a wooden mat"></div>
  <div class="tile t3" role="img" aria-label="Portrait of a woman with glowing skin on a blush background"></div>
  <div class="tile t4" role="img" aria-label="Bath basket with soap bars, salt and a brush"></div>
  <div class="tile t5" role="img" aria-label="Hands holding a bowl of cream beside serum bottles"><span class="zoom"></span></div>
  <div class="tile t6" role="img" aria-label="Hand holding a skincare spray bottle"></div>
  <div class="tile t7" role="img" aria-label="Coconut halves and natural soap">Lorem ipsum dolor sit amet,<br>consectetur adipiscing elit,</div>
  <div class="tile t8" role="img" aria-label="Natural spa products on a stone surface">Lorem ipsum dolor sit amet, consectetur<br>adipiscing elit, sed do eiusmod tempor</div>
</div>

<section class="abs about">
  <div class="abs about-photo" role="img" aria-label="Candle, leaves, cream jars and a honey dipper on an aqua surface"></div>
  <div class="abs about-body">
    <h2>ABOUT US</h2>
    <div class="rule"></div>
    <p>Have the copy on this strip read “They say that home is where the heart is. But home is also where your mind and body reside. At Bright Nook we believe that home should be your place of Zen. A respite from the craz world outside those walls. It is where you recharge your soul so you can approach each day with the focus and energy necessary to conquer the world.</p>
    <span class="btn-outline">Tell Me More <svg width="12" height="12" viewBox="0 0 12 12" fill="none" stroke="#222" stroke-width="2"><path d="M1 2l4 4-4 4M6 2l4 4-4 4"/></svg></span>
  </div>
</section>

<div class="abs section-title" style="top:2052px">
  <h2>THE HAPPY BLOG</h2>
  <div class="rule"></div>
  <p>Food for the mind, tips for the body and exercises for the soul</p>
</div>

<article class="abs card c1" style="left:111px">
  <div class="img" role="img" aria-label="Pink pouch filled with bath bombs and beauty tools"></div>
  <div class="body">
    <h3>Lorem ipsum dolor sit amet,</h3>
    <div class="meta"><span><svg width="14" height="14" viewBox="0 0 14 14" fill="none" stroke="#2fb5bf" stroke-width="1.5"><rect x="1" y="2" width="12" height="11"/><path d="M1 5h12M4 0v3M10 0v3"/></svg>May 3</span><span><svg width="16" height="14" viewBox="0 0 16 14" fill="none" stroke="#2fb5bf" stroke-width="1.5"><ellipse cx="8" cy="6" rx="7" ry="5"/><path d="M4 10l-2 3 4-2"/></svg>comment</span></div>
    <p>Lorem ipsum dolor sit&nbsp; consectetur adipiscing elit, sed do eiusmod tempor incididunt ut labore et dolore magna</p>
    <div class="more">Read More <svg width="10" height="10" viewBox="0 0 12 12" fill="none" stroke="#2fb5bf" stroke-width="2"><path d="M1 2l4 4-4 4M6 2l4 4-4 4"/></svg></div>
  </div>
</article>
<article class="abs card c2" style="left:449px">
  <div class="img" role="img" aria-label="Woman applying cream at a bright table"></div>
  <div class="body">
    <h3>Lorem ipsum dolor sit amet,</h3>
    <div class="meta"><span><svg width="14" height="14" viewBox="0 0 14 14" fill="none" stroke="#2fb5bf" stroke-width="1.5"><rect x="1" y="2" width="12" height="11"/><path d="M1 5h12M4 0v3M10 0v3"/></svg>May 3</span><span><svg width="16" height="14" viewBox="0 0 16 14" fill="none" stroke="#2fb5bf" stroke-width="1.5"><ellipse cx="8" cy="6" rx="7" ry="5"/><path d="M4 10l-2 3 4-2"/></svg>comment</span></div>
    <p>Lorem ipsum dolor sit&nbsp; consectetur adipiscing elit, sed do eiusmod tempor incididunt ut labore et dolore magna</p>
    <div class="more">Read More <svg width="10" height="10" viewBox="0 0 12 12" fill="none" stroke="#2fb5bf" stroke-width="2"><path d="M1 2l4 4-4 4M6 2l4 4-4 4"/></svg></div>
  </div>
</article>
<article class="abs card c3" style="left:787px">
  <div class="img" role="img" aria-label="Glass jars of oil and cream with flowers"></div>
  <div class="body">
    <h3>Lorem ipsum dolor sit amet,</h3>
    <div class="meta"><span><svg width="14" height="14" viewBox="0 0 14 14" fill="none" stroke="#2fb5bf" stroke-width="1.5"><rect x="1" y="2" width="12" height="11"/><path d="M1 5h12M4 0v3M10 0v3"/></svg>May 3</span><span><svg width="16" height="14" viewBox="0 0 16 14" fill="none" stroke="#2fb5bf" stroke-width="1.5"><ellipse cx="8" cy="6" rx="7" ry="5"/><path d="M4 10l-2 3 4-2"/></svg>comment</span></div>
    <p>Lorem ipsum dolor sit&nbsp; consectetur adipiscing elit, sed do eiusmod tempor incididunt ut labore et dolore magna</p>
    <div class="more">Read More <svg width="10" height="10" viewBox="0 0 12 12" fill="none" stroke="#2fb5bf" stroke-width="2"><path d="M1 2l4 4-4 4M6 2l4 4-4 4"/></svg></div>
  </div>
</article>

<section class="abs paylater">
  <h2>DON’T SWEAT IT YOU CAN PAY LATER</h2>
  <div class="rule"></div>
  <p>Lorem ipsum dolor sit amet, consectetur adipiscing elit, sed do eiusmod tempor incididunt ut labore et dolore magna aliqua. Ut enim ad minim veniam, quis nostrud exercitation</p>
  <div class="payname"><i></i>Loafly</div>
</section>

<footer class="abs footer">
  <div class="abs brand"><i></i>BrightNook</div>
  <div class="abs social"><span class="dot"></span><span class="dot"></span><span class="dot"></span><span class="dot"></span></div>
  <div class="abs fcol" style="left:379px">
    <h4>Quicklinks</h4>
    <ul><li>Home</li><li>About Us</li><li>Featured Product</li><li>Blog</li><li>Contact Us</li></ul>
  </div>
  <div class="abs fcol" style="left:615px">
    <h4>Otherlinks</h4>
    <ul><li>FAQ</li><li>Services</li><li>Team</li><li>Privacy</li><li>Policy</li></ul>
  </div>
  <div class="abs fcol news" style="left:811px">
    <h4>Sign up for our newsletter</h4>
    <p>Lorem ipsum dolor sit amet, consectetur adipiscing elit, sed do eiusmod tempor.</p>
    <div class="email"><svg width="14" height="11" viewBox="0 0 14 11" fill="none" stroke="#999" stroke-width="1.3"><rect x=".7" y=".7" width="12.6" height="9.6"/><path d="M1 1l6 5 6-5"/></svg>Enter Your Email:</div>
    <div class="submit">SUBMIT <svg width="14" height="14" viewBox="0 0 14 14"><circle cx="7" cy="7" r="7" fill="#fff"/><path d="M6 4l3 3-3 3" stroke="#3a1d8c" stroke-width="1.8" fill="none"/></svg></div>
  </div>
  <div class="abs divider"></div>
  <div class="abs copy">©Copyright 2021 Bright Nook.All right reserved.</div>
  <svg class="abs chat" width="48" height="40" viewBox="0 0 48 40" fill="none" stroke="#2fb5bf" stroke-width="3"><path d="M24 3C12 3 3 10 3 18c0 5 3 9 8 12l-2 8 9-5c2 .5 4 .6 6 .6 12 0 21-7 21-15.6S36 3 24 3z"/><circle cx="15" cy="18" r="2.5" fill="#2fb5bf"/><circle cx="24" cy="18" r="2.5" fill="#2fb5bf"/><circle cx="33" cy="18" r="2.5" fill="#2fb5bf"/></svg>
</footer>

</body>
</html>
```